Tallow Brook Digital Advertisement

This project is a request for a unique ad picture and message for Tallow Brook that will grab the audience instantly. Tallow Brook is a turn-around specialist and mobile online marketing agency. We create sustainable digital beach-heads (brand + value prop). Our tagline = Digital Builders. Our website is located at: tallowbrook.net

Target Market(s)

small and medium business owners and leadership team

Requirements
Must have
• Key Messages: 1) TAP INTO THE RIGHT TRAFFIC 2) "Instinct is Correct. 7 out of 10 CEOs believe they're wasting advertising & marketing money" (Vantell) 3) Tallow Brook uses a proven and trademarked algorithm for growth.

```html
<!DOCTYPE html>
<html lang="en">
<head>
<meta charset="utf-8">
<title>Tallow Brook – Digital Builders Poster</title>
<link rel="stylesheet" href="https://fonts.googleapis.com/css2?family=Montserrat:wght@400;500;700;800&display=swap">
<style>
  :root {
    --page-bg: #e9e9ec;
    --paper-light: #f7f7f8;
    --paper-shade: #e6e6e9;
    --indigo-deep: #150a86;
    --indigo: #3a1f94;
    --headline-dark: #2f1c8c;
    --headline-purple: #5a2d9c;
    --ink: #333333;
    --rule: #9a9a9a;
    --white: #ffffff;
  }
  * { margin: 0; padding: 0; box-sizing: border-box; }
  html, body {
    width: 683px;
    height: 1200px;
    overflow: hidden;
    background: var(--page-bg);
  }
  .canvas {
    position: relative;
    width: 683px;
    height: 1200px;
  }
  .poster {
    position: absolute;
    left: 21px;
    top: 148px;
    width: 640px;
    height: 904px;
    box-shadow: 0 6px 18px rgba(0, 0, 0, 0.18);
  }
  .poster svg { display: block; }
  .headline { font-family: "Montserrat", sans-serif; font-weight: 800; }
  .headline-top { fill: var(--headline-dark); }
  .headline-bottom { fill: var(--headline-purple); }
  .brand-name {
    font-family: "Montserrat", sans-serif;
    font-weight: 800;
    fill: var(--ink);
  }
  .traffic-line {
    font-family: "Montserrat", sans-serif;
    font-weight: 800;
    fill: var(--headline-dark);
  }
  .stat-lead {
    font-family: "Montserrat", sans-serif;
    font-weight: 800;
    fill: var(--headline-purple);
  }
  .stat-body {
    font-family: "Montserrat", sans-serif;
    font-weight: 500;
    fill: var(--ink);
  }
  .lead-in {
    font-family: "Montserrat", sans-serif;
    font-weight: 500;
    fill: var(--ink);
  }
  .method-name {
    font-family: "Montserrat", sans-serif;
    font-weight: 800;
    fill: var(--headline-purple);
  }
  .web-address {
    font-family: "Montserrat", sans-serif;
    font-weight: 500;
    fill: var(--white);
  }
</style>
</head>
<body>
<main class="canvas">
  <section class="poster" aria-label="Tallow Brook Digital Builders poster">
    <svg width="640" height="904" viewBox="0 0 640 904" xmlns="http://www.w3.org/2000/svg">
      <defs>
        <linearGradient id="paper-fill" x1="0" y1="0" x2="1" y2="1">
          <stop offset="0" stop-color="var(--paper-shade)"/>
          <stop offset="0.5" stop-color="var(--paper-light)"/>
          <stop offset="1" stop-color="var(--white)"/>
        </linearGradient>
        <linearGradient id="wave-fill" x1="0" y1="0" x2="1" y2="1">
          <stop offset="0" stop-color="var(--indigo)"/>
          <stop offset="1" stop-color="var(--indigo-deep)"/>
        </linearGradient>
        <linearGradient id="art-fill" x1="0" y1="0" x2="1" y2="1">
          <stop offset="0" stop-color="#f3e6d0"/>
          <stop offset="0.5" stop-color="#dcdcee"/>
          <stop offset="1" stop-color="#c9cae6"/>
        </linearGradient>
      </defs>

      <rect class="paper" width="640" height="904" fill="url(#paper-fill)"/>

      <path class="wave-top" fill="url(#wave-fill)"
        d="M0,0 H267 C238,18 205,38 176,80 C148,122 150,150 132,190 C114,228 66,232 48,262 C32,288 34,300 0,305 Z"/>

      <path class="wave-bottom" fill="url(#wave-fill)"
        d="M640,597 V904 H375 C420,882 500,862 530,812 C560,762 560,738 580,700 C600,660 612,618 640,597 Z"/>

      <g class="brand-mark">
        <rect x="255" y="54" width="127" height="146" fill="none" stroke="var(--ink)" stroke-width="1.5"/>
        <text class="brand-name" x="318.5" y="134" text-anchor="middle" font-size="17"
          textLength="106" lengthAdjust="spacingAndGlyphs">Tallow Brook</text>
      </g>

      <text class="headline headline-top" x="320" y="296" text-anchor="middle" font-size="74"
        textLength="314" lengthAdjust="spacingAndGlyphs">DIGITAL</text>
      <text class="headline headline-bottom" x="320" y="368" text-anchor="middle" font-size="74"
        textLength="374" lengthAdjust="spacingAndGlyphs">BUILDERS</text>

      <text class="traffic-line" x="320" y="402" text-anchor="middle" font-size="17"
        textLength="300" lengthAdjust="spacingAndGlyphs">TAP INTO THE RIGHT TRAFFIC</text>

      <rect class="illustration" x="107" y="418" width="426" height="248" rx="18" fill="url(#art-fill)"
        role="img" aria-label="Flat illustration of two people using phones beside a large smartphone showing a search screen, with gears and a light bulb"/>

      <g class="ceo-stat">
        <text class="stat-lead" x="320" y="690" text-anchor="middle" font-size="13.5">INSTINCT IS CORRECT.</text>
        <text class="stat-body" x="320" y="708" text-anchor="middle" font-size="12"
          textLength="370" lengthAdjust="spacingAndGlyphs">7 out of 10 CEOs believe they're wasting advertising</text>
        <text class="stat-body" x="320" y="724" text-anchor="middle" font-size="12">&amp; marketing money (Vantell)</text>
      </g>

      <text class="lead-in" x="307" y="763" text-anchor="middle" font-size="10.5"
        textLength="372" lengthAdjust="spacingAndGlyphs">TALLOW BROOK USES A PROVEN, TRADEMARKED GROWTH ALGORITHM CALLED THE</text>
      <line class="lead-in-rule" x1="120" y1="773" x2="494" y2="773" stroke="var(--rule)" stroke-width="1"/>

      <text class="method-name" x="306" y="807" text-anchor="middle" font-size="38"
        textLength="290" lengthAdjust="spacingAndGlyphs">9K FRAMEWORK</text>

      <text class="web-address" x="612" y="882" text-anchor="end" font-size="17"
        textLength="186" lengthAdjust="spacingAndGlyphs">www.tallowbrook.net</text>
    </svg>
  </section>
</main>
</body>
</html>
```